Corvane Freight Company Business Card Design

We are a company that delivers natural saltwater (from the ocean) to aquarium companies, restaurants and home marine tanks. I would like a new business card to suit.

Must include Name, company name, abn, contact number and website as well as logo (see attached).

Looking for a design that stands out, has a clean but unique appearance.

Double and single sided entries welcome

Business

• Logo

```html
<!DOCTYPE html>
<html lang="en">
<head>
<meta charset="utf-8">
<title>Corvane Freight Company – Business Card</title>
<link rel="stylesheet" href="https://fonts.googleapis.com/css2?family=Source+Sans+3:wght@400;600;700&display=swap">
<style>
  :root {
    --stage: #1c1c1c;
    --card-front: #2176e8;
    --card-back: #3db4f6;
    --band: #3db4f6;
    --white: #ffffff;
    --soft-white: #e8f3ff;
  }
  * { margin: 0; padding: 0; box-sizing: border-box; }
  html, body {
    width: 1200px;
    height: 407px;
    overflow: hidden;
    background: var(--stage);
    font-family: "Source Sans 3", "Myriad Pro", Arial, sans-serif;
    color: var(--white);
  }
  .canvas {
    position: relative;
    width: 1200px;
    height: 407px;
  }
  .card {
    position: absolute;
    top: 57px;
    width: 519px;
    height: 296px;
    overflow: hidden;
  }
  .card--front { left: 50px; background: var(--card-front); }
  .card--back { left: 615px; background: var(--card-back); }

  .brand-name {
    position: absolute;
    left: 0;
    width: 100%;
    text-align: center;
    font-weight: 700;
    font-size: 42px;
    letter-spacing: -0.5px;
    color: var(--white);
    line-height: 1;
  }
  .card--front .brand-name { top: 72px; }
  .card--back .brand-name { top: 114px; }

  .name-band {
    position: absolute;
    left: 0;
    top: 165px;
    width: 100%;
    height: 43px;
    border-top: 2px solid var(--soft-white);
    border-bottom: 2px solid var(--soft-white);
    padding: 3px 0;
    background: var(--card-front);
  }
  .name-band__fill {
    height: 100%;
    background: var(--band);
    display: flex;
    align-items: center;
    justify-content: center;
    font-size: 15px;
  }
  .name-band__name { font-weight: 700; }
  .name-band__title { font-weight: 400; font-size: 13px; margin-left: 4px; }

  .details {
    position: absolute;
    top: 228px;
    left: 0;
    width: 100%;
    font-size: 13px;
    line-height: 18px;
  }
  .address {
    position: absolute;
    right: 266px;
    text-align: right;
    font-style: normal;
  }
  .address__company { font-weight: 700; }
  .divider {
    position: absolute;
    left: 270px;
    top: 0;
    width: 1px;
    height: 58px;
    background: var(--soft-white);
  }
  .contact {
    position: absolute;
    left: 283px;
    list-style: none;
  }
  .contact li { display: flex; align-items: center; gap: 5px; }
  .contact svg { width: 10px; height: 10px; flex: none; }

  .website-back {
    position: absolute;
    left: 0;
    top: 238px;
    width: 100%;
    text-align: center;
    font-size: 16px;
    letter-spacing: 3px;
  }
</style>
</head>
<body>
<main class="canvas">
  <section class="card card--front" aria-label="Card front">
    <p class="brand-name">Corvane Freight</p>

    <div class="name-band">
      <div class="name-band__fill">
        <span class="name-band__name">Your name,</span><span class="name-band__title">Title</span>
      </div>
    </div>

    <div class="details">
      <address class="address">
        <div class="address__company">Corvane Freight Company</div>
        <div>Street Name, City Name</div>
        <div>State, City Zip Code</div>
      </address>
      <span class="divider"></span>
      <ul class="contact">
        <li>
          <svg viewBox="0 0 10 10" aria-hidden="true"><circle cx="5" cy="5" r="4.3" fill="none" stroke="#fff" stroke-width="1"/><path d="M3.3 2.6c.3-.3.6-.2.8.1l.5.8c.1.3 0 .5-.2.6l-.3.2c.2.6.7 1.1 1.3 1.4l.2-.3c.2-.2.4-.3.6-.1l.8.5c.3.2.3.5.1.8-.6.7-1.6.6-2.6-.2-1-.9-1.6-2-1.2-2.8z" fill="#fff"/></svg>
          123-456-7890
        </li>
        <li>
          <svg viewBox="0 0 10 10" aria-hidden="true"><circle cx="5" cy="5" r="4.5" fill="#fff"/><path d="M.7 5h8.6M5 .6c-2 2.6-2 6.2 0 8.8M5 .6c2 2.6 2 6.2 0 8.8" fill="none" stroke="#2176e8" stroke-width=".7"/></svg>
          www.website.com
        </li>
        <li>ABN : 0123456789</li>
      </ul>
    </div>
  </section>

  <section class="card card--back" aria-label="Card back">
    <p class="brand-name">Corvane Freight</p>
    <p class="website-back">www.website.com</p>
  </section>
</main>
</body>
</html>
```